Tovella Fireworks needs a web design and logo

We need a web design and logo for a fireworks business in Sydney Australia, we do public display, weddings, tv, theatrical, clubs and any other organisation that wants to do something special.
Name is Marrowind Fireworks & Pyrotechnics

```html
<!DOCTYPE html>
<html lang="en">
<head>
<meta charset="utf-8">
<title>Marrowind Fireworks &amp; Pyrotechnics</title>
<link rel="stylesheet" href="https://fonts.googleapis.com/css2?family=PT+Sans:wght@400;700&family=Arimo:wght@400;700&display=swap">
<style>
  :root {
    --page-bg: #383838;
    --footer-bg: #1e1e1e;
    --red-top: #f0141c;
    --red-bottom: #b30006;
    --red-dot: #d8000a;
    --panel: #ffffff;
    --panel-line: #cfcfcf;
    --ink: #222222;
    --body-ink: #555555;
    --footer-ink: #b8b8b8;
    --slider-bar: #e6e6e6;
    --warm-glow: rgba(255, 170, 70, 0.5);
    --cool-glow: rgba(90, 170, 255, 0.25);
    --green-glow: rgba(170, 220, 90, 0.28);
  }
  * { box-sizing: border-box; margin: 0; padding: 0; }
  html, body { width: 1074px; height: 1200px; overflow: hidden; }
  body {
    position: relative;
    font-family: "PT Sans", sans-serif;
    background:
      radial-gradient(ellipse 330px 240px at 600px 700px, var(--warm-glow), transparent 70%),
      radial-gradient(ellipse 260px 300px at 980px 280px, var(--cool-glow), transparent 70%),
      radial-gradient(ellipse 200px 180px at 1000px 820px, var(--green-glow), transparent 70%),
      radial-gradient(ellipse 240px 200px at 300px 120px, rgba(255,120,60,0.2), transparent 70%),
      radial-gradient(ellipse 700px 600px at 540px 560px, #4a4644, var(--page-bg) 75%);
  }
  .site-title {
    position: absolute; left: 93px; top: 50px;
    font-size: 26px; line-height: 34px; color: #fff; font-weight: 400;
  }
  .main-nav {
    position: absolute; left: 95px; top: 126px; width: 886px; height: 37px;
    background: linear-gradient(var(--red-top), var(--red-bottom));
    border-radius: 4px; border: 1px solid #8a0004;
  }
  .main-nav a {
    position: absolute; top: 10px; font-size: 13.5px; line-height: 16px; color: #fff; text-decoration: none;
  }
  .nav-divider { position: absolute; top: 7px; width: 1px; height: 22px; background: rgba(255,255,255,0.25); }
  .search {
    position: absolute; left: 734px; top: 4px; width: 141px; height: 27px;
    background: #fff; border-radius: 14px;
  }
  .search svg { position: absolute; left: 11px; top: 6px; }
  .search span { position: absolute; left: 36px; top: 6px; font-size: 12px; line-height: 15px; color: #999; }
  .slider {
    position: absolute; left: 95px; top: 193px; width: 885px; height: 369px;
    border: 1px solid #9a9a9a; background: var(--slider-bar);
  }
  .slide-photo {
    height: 337px;
    background: linear-gradient(#2e2a32, #1e1c22);
  }
  .slider-dots { position: absolute; right: 26px; bottom: 10px; display: flex; gap: 5px; }
  .slider-dots span { width: 12px; height: 12px; background: #fff; border: 1px solid #aaa; }
  .slider-dots .active { background: var(--red-dot); border-color: var(--red-dot); }
  .service-card {
    position: absolute; top: 607px; width: 282px; height: 234px;
    background: var(--panel); border: 1px solid var(--panel-line);
  }
  .service-card h2 {
    position: absolute; left: 36px; top: 17px;
    font-family: "Arimo", sans-serif; font-size: 17px; line-height: 20px; font-weight: 700; color: var(--ink);
  }
  .service-photo { position: absolute; left: 38px; top: 49px; width: 204px; height: 103px; }
  .service-card p {
    position: absolute; left: 38px; top: 196px; margin-top: -28px; width: 220px;
    font-size: 9.4px; line-height: 17px; color: var(--body-ink); white-space: nowrap;
  }
  .about-panel {
    position: absolute; left: 95px; top: 884px; width: 887px; height: 184px;
    background: var(--panel); border: 1px solid var(--panel-line);
  }
  .about-panel h2, .newsletter h2 {
    position: absolute; font-family: "Arimo", sans-serif; font-size: 17px; line-height: 20px; font-weight: 700; color: var(--ink);
  }
  .about-panel > h2 { left: 27px; top: 19px; }
  .about-photo {
    position: absolute; left: 28px; top: 51px; width: 137px; height: 91px;
    background: linear-gradient(#2a2030, #3a2024);
  }
  .about-panel p {
    position: absolute; left: 183px; top: 58px; width: 400px;
    font-size: 12.2px; line-height: 20px; color: var(--body-ink); white-space: nowrap;
  }
  .newsletter { position: absolute; left: 611px; top: 0; width: 260px; height: 100%; }
  .newsletter h2 { left: 0; top: 26px; }
  .field {
    position: absolute; left: 3px; width: 248px; height: 26px;
    border: 1px solid #c8c8c8; font-size: 12px; line-height: 14px; color: #666; padding: 5px 0 0 11px;
  }
  .submit {
    position: absolute; left: 153px; top: 137px; width: 98px; height: 28px;
    border: 1px solid #aaa; border-radius: 2px; background: linear-gradient(#f4f4f4, #cfcfcf);
    font-size: 14px; color: #333; text-align: center; line-height: 26px;
  }
  .site-footer {
    position: absolute; left: 0; top: 1111px; width: 1074px; height: 89px; background: var(--footer-bg);
  }
  .footer-links { position: absolute; left: 83px; top: 22px; font-size: 11.5px; line-height: 14px; color: var(--footer-ink); }
  .footer-links span { margin: 0 7px; }
  .copyright { position: absolute; left: 82px; top: 51px; font-size: 10.5px; line-height: 13px; color: #9a9a9a; }
  .social { position: absolute; left: 879px; top: 33px; display: flex; gap: 1px; }
  .social span { width: 22px; height: 22px; }
</style>
</head>
<body>
  <h1 class="site-title">Marrowind Fireworks &amp; Pyrotechnics</h1>

  <nav class="main-nav">
    <a href="#" style="left:27px">Home</a>
    <span class="nav-divider" style="left:94px"></span>
    <a href="#" style="left:118px">About Us</a>
    <span class="nav-divider" style="left:203px"></span>
    <a href="#" style="left:228px">Services</a>
    <span class="nav-divider" style="left:306px"></span>
    <a href="#" style="left:334px">Blog</a>
    <span class="nav-divider" style="left:388px"></span>
    <a href="#" style="left:415px">Support</a>
    <span class="nav-divider" style="left:495px"></span>
    <a href="#" style="left:518px">Contact</a>
    <div class="search">
      <svg width="18" height="16" viewBox="0 0 18 16"><circle cx="6" cy="6" r="4.5" fill="none" stroke="#777" stroke-width="2"/><line x1="9.5" y1="9.5" x2="15" y2="14" stroke="#777" stroke-width="3" stroke-linecap="round"/></svg>
      <span>Search</span>
    </div>
  </nav>

  <section class="slider">
    <div class="slide-photo" role="img" aria-label="Photo: harbour city skyline at night with fireworks over boats on the water"></div>
    <div class="slider-dots"><span></span><span class="active"></span><span></span><span></span></div>
  </section>

  <article class="service-card" style="left:96px">
    <h2>Weddings</h2>
    <div class="service-photo" role="img" aria-label="Photo: red fireworks over an evening wedding crowd" style="background:linear-gradient(#2a1414,#140c0c)"></div>
    <p>Lorem ipsum dolor sit amet, consectetur adipi-<br>scing elit, sed do eiusmod tempor incididunt ut<br>labore et enim ad minim</p>
  </article>
  <article class="service-card" style="left:397px">
    <h2>Theatrical</h2>
    <div class="service-photo" role="img" aria-label="Photo: blue and white fireworks above a stage audience" style="background:linear-gradient(#0e1822,#1e2e3a)"></div>
    <p>Lorem ipsum dolor sit amet, consectetur adipi-<br>scing elit, sed do eiusmod tempor incididunt ut<br>labore et enim ad minim</p>
  </article>
  <article class="service-card" style="left:698px">
    <h2>Club</h2>
    <div class="service-photo" role="img" aria-label="Photo: teal fireworks over a club crowd" style="background:linear-gradient(#1c3a36,#0c1614)"></div>
    <p>Lorem ipsum dolor sit amet, consectetur adipi-<br>scing elit, sed do eiusmod tempor incididunt ut<br>labore et enim ad minim</p>
  </article>

  <section class="about-panel">
    <h2>Marrowind Fireworks &amp; Pyrotechnics</h2>
    <div class="about-photo" role="img" aria-label="Photo: firework over a city skyline at night"></div>
    <p>Sed ut perspiciatis unde omnis iste natus error sit voluptatem<br>accusantium doloremque laudantium, totam rem aperiam, eaque<br>ipsa quae ab illo inventore veritatis et quasi architecto beatae<br>vitae dicta sunt explicabo nemo enim</p>
    <div class="newsletter">
      <h2>Newsletter Sign up</h2>
      <div class="field" style="top:64px">Name*</div>
      <div class="field" style="top:103px">Email*</div>
      <div class="submit">Submit</div>
    </div>
  </section>

  <footer class="site-footer">
    <div class="footer-links">Home<span>|</span>About us<span>|</span>Services<span>|</span>Blog<span>|</span>Support<span>|</span>Contact us</div>
    <div class="copyright">Copyright © 2015 Marrowind Fireworks &amp; Pyrotechnics . All right reserved.</div>
    <div class="social" aria-label="Social links">
      <span style="background:#f39c12"></span>
      <span style="background:#3a9ad9"></span>
      <span style="background:#2a4a8a"></span>
      <span style="background:#2a6ad0"></span>
      <span style="background:#2a8ac0"></span>
    </div>
  </footer>
</body>
</html>
```